brightquokka.net we need a webpage designed for our new product

We need a webpage designed for our new range of products from our new brand. We have had a logo designed on sketchharbor (see attached) and we want to keep to this theme. Our first product is a range of affordable app controlled LED lightbulbs.

I have added some photos that we think is good inspirational material and would be good as a background to this website, but we want the site to look modern but not conventional. We would like something that makes our company look quirky not corporate.

Thats it

Target Market(s)

Our product is being stocked by big name online retailers in the UK, the page will get link through hits from our app. Our target market is gadget freaks of all ages.

Industry/Entity Type

It Company

Requirements
Must have
• We are going to need a help page, text to be uploaded next few days.

We need a contact page.

design my work on iOS and Android as most people will access page through their handset or tablet.
Should not have
• We do not want anything too corporate.

```html
<!DOCTYPE html>
<html lang="en">
<head>
<meta charset="utf-8">
<title>brightquokka.net – Smart LED</title>
<link rel="stylesheet" href="https://fonts.googleapis.com/css2?family=Open+Sans:wght@400;700&family=Michroma&family=Carlito:ital,wght@0,400;0,700;1,400;1,700&family=Raleway:wght@400&family=Ubuntu:wght@500&family=Roboto:wght@300&family=Arimo:ital,wght@1,700&display=swap">
<style>
:root{
  --green:#3fac48;
  --green-dark:#2f8f38;
  --panel:rgba(78,78,78,.93);
  --white:#ffffff;
  --grey-text:#5a5a5a;
  --light-grey:#8a8a8a;
  --frame:#c9c9c9;
}
*{margin:0;padding:0;box-sizing:border-box}
html,body{width:1200px;height:1156px;overflow:hidden;background:var(--white)}
body{position:relative;font-family:"Carlito",sans-serif}

.top-nav{position:absolute;left:0;top:0;width:1200px;height:58px;background:var(--green)}
.top-nav ul{list-style:none}
.top-nav li{position:absolute;top:20px;font:700 12.5px "Open Sans",sans-serif;color:var(--white);letter-spacing:.3px}
.top-nav .phone{position:absolute;left:902px;top:14px;font:400 23px "Open Sans",sans-serif;color:var(--white)}

.hero{position:absolute;left:0;top:58px;width:1200px;height:460px;
  background:linear-gradient(180deg,#8a6a4a 0%,#6e6a66 30%,#a9392e 55%,#5d4a3a 80%,#3b2f28 100%)}
.hero-pitch{position:absolute;left:100px;top:112px;width:422px;height:248px;background:var(--panel);border-radius:6px}
.hero-pitch h1{position:absolute;left:19px;top:26px;font:400 22px "Michroma",sans-serif;line-height:30px;color:var(--green);letter-spacing:-.3px}
.hero-pitch h1 span{color:#eeeeee}
.hero-pitch ul{list-style:none;position:absolute;left:19px;top:104px}
.hero-pitch li{position:relative;height:28px;padding-left:42px;color:var(--white);font-size:13.5px;white-space:nowrap}
.hero-pitch li b{font-weight:400;font-size:17px;color:#e6e6e6}
.hero-pitch li svg{position:absolute;left:0;top:2px}

.contact-card{position:absolute;left:600px;top:112px;width:422px;height:158px;background:var(--white);border-radius:8px}
.contact-card .brand{position:absolute;left:18px;top:16px;width:180px;height:134px;text-align:center}
.brand-dot{display:block;width:44px;height:44px;border-radius:50%;background:var(--green);margin:22px auto 22px}
.brand-name{font:400 12px "Michroma",sans-serif;color:var(--green);letter-spacing:.5px}
.contact-card .divider{position:absolute;left:199px;top:20px;width:1px;height:132px;background:#d8d8d8}
.contact-card address{position:absolute;left:211px;top:28px;font-style:normal;font-family:"Raleway",sans-serif;color:var(--grey-text)}
.contact-card .mail{font-size:14.5px;color:var(--green)}
.contact-card .tel{font-size:14px;margin-top:8px}
.contact-card .post{font-size:13px;line-height:22px;margin-top:9px}

.zigzag{position:absolute;left:0;top:508px}

.products{position:absolute;left:0;top:528px;width:1200px;height:362px;background:var(--green)}
.products h2{position:absolute;left:0;top:46px;width:1184px;text-align:center;font:400 21px "Michroma",sans-serif;color:var(--white)}
.product{position:absolute;top:106px;width:172px}
.product .shot{width:172px;height:148px;border:3px solid var(--frame);background:radial-gradient(circle at 45% 50%,#7d7f84 0%,#c9cacd 38%,#ffffff 62%)}
.product .label{margin-top:20px;height:35px;background:var(--white);font:300 18px "Roboto",sans-serif;color:var(--green);padding:6px 0 0 33px}

.site-footer{position:absolute;left:0;top:890px;width:1200px;height:266px}
.footer-brand{position:absolute;left:120px;top:40px;width:190px;text-align:center}
.footer-brand .brand-dot{width:60px;height:60px;margin:22px auto 68px}
.footer-brand .brand-name{font-size:14px}

.testimonial{position:absolute;left:410px;top:44px;width:276px}
.testimonial h3{position:absolute;left:72px;top:8px;font:500 20px "Ubuntu",sans-serif;color:#555}
.testimonial .quote-mark{position:absolute;left:0;top:78px;font:700 20px Georgia,serif;color:#777}
.testimonial blockquote{position:absolute;left:22px;top:88px;width:254px;font:italic 13.5px/22px "Carlito",sans-serif;color:#666;text-align:justify}
.testimonial cite{position:absolute;left:22px;top:200px;font:italic 700 13.5px "Carlito",sans-serif;color:var(--green-dark);text-decoration:underline}

.newsletter{position:absolute;left:772px;top:38px;width:296px}
.newsletter h3{position:absolute;left:48px;top:10px;font:500 20px "Ubuntu",sans-serif;color:#555;white-space:nowrap}
.newsletter p{position:absolute;left:8px;top:51px;width:268px;font:italic 700 12px/14px "Arimo",sans-serif;color:var(--light-grey);text-align:justify}
.newsletter .field{position:absolute;left:0;top:94px;width:295px;height:34px;border-radius:17px;border:1px solid #dcdcdc;background:linear-gradient(#ececec,#fafafa);font:12.5px "Arimo",sans-serif;font-style:normal;color:#888;padding:9px 0 0 16px}
.social{position:absolute;left:4px;top:144px;display:flex;gap:5px}
.social span{width:31px;height:31px;border-radius:50%;border:2px solid #d6d6d6}
.subscribe{position:absolute;left:216px;top:146px;width:79px;height:28px;border-radius:10px;background:linear-gradient(#5cc257,#3a9e36);color:var(--white);font:12.5px "Arimo",sans-serif;text-align:center;line-height:28px}

.base-line{position:absolute;left:0;top:1151px;width:1200px;height:5px;background:var(--green)}
</style>
</head>
<body>

<nav class="top-nav">
  <ul>
    <li style="left:109px">HOME</li>
    <li style="left:194px">ABOUT US</li>
    <li style="left:304px">BUY LED</li>
    <li style="left:406px">WHY LED</li>
    <li style="left:509px">WHICH LED</li>
    <li style="left:630px">FAQ</li>
    <li style="left:701px">CONTACT US</li>
  </ul>
  <div class="phone">+44 (0)1632 960418</div>
</nav>

<header class="hero" role="img" aria-label="Photo of a vintage toy and collectibles shop with pedal cars, radios and ornaments"></header>

<section class="hero-pitch">
  <h1>LED - A Green Technology<br><span>love Influencing</span></h1>
  <ul>
    <li><svg width="20" height="18" viewBox="0 0 20 18"><path d="M1 10 L7 16 L19 2" fill="none" stroke="#3fac48" stroke-width="4" stroke-linecap="round"/></svg><b>Get Found :</b> Help Prospects find you online</li>
    <li><svg width="20" height="18" viewBox="0 0 20 18"><path d="M1 10 L7 16 L19 2" fill="none" stroke="#3fac48" stroke-width="4" stroke-linecap="round"/></svg><b>Covert :</b> Nurture your leads and drive conversions</li>
    <li><svg width="20" height="18" viewBox="0 0 20 18"><path d="M1 10 L7 16 L19 2" fill="none" stroke="#3fac48" stroke-width="4" stroke-linecap="round"/></svg><b>Analyze :</b> Measure and improve your marketing</li>
    <li><svg width="20" height="18" viewBox="0 0 20 18"><path d="M1 10 L7 16 L19 2" fill="none" stroke="#3fac48" stroke-width="4" stroke-linecap="round"/></svg><b>Integrate :</b> Access the marketplace for apps and integration</li>
  </ul>
</section>

<section class="contact-card">
  <div class="brand"><span class="brand-dot"></span><span class="brand-name">BRIGHTQUOKKA</span></div>
  <div class="divider"></div>
  <address>
    <div class="mail">hello@brightquokka.net</div>
    <div class="tel">+(44) 163 296 0521</div>
    <div class="post">Lantern Row Studios<br>18 Mill Yard, Unit 4<br>Newark, NG24 1ZZ</div>
  </address>
</section>

<svg class="zigzag" width="1200" height="22" viewBox="0 0 1200 22">
  <pattern id="teeth" width="8" height="6" patternUnits="userSpaceOnUse"><path d="M0 6 L4 0 L8 6 Z" fill="#ffffff"/></pattern>
  <rect x="0" y="0" width="1200" height="6" fill="url(#teeth)"/>
  <rect x="0" y="6" width="1200" height="10" fill="#ffffff"/>
  <rect x="0" y="16" width="1200" height="6" fill="url(#teeth)" transform="rotate(180 600 19)"/>
</svg>

<section class="products">
  <h2>Lorem Ipsum Dolor</h2>
  <div class="product" style="left:116px"><div class="shot" role="img" aria-label="LED spotlight bulb"></div><div class="label">Product 1</div></div>
  <div class="product" style="left:315px"><div class="shot" role="img" aria-label="LED globe bulb with screw base"></div><div class="label">Product 2</div></div>
  <div class="product" style="left:514px"><div class="shot" role="img" aria-label="White LED bulb with finned body"></div><div class="label">Product 3</div></div>
  <div class="product" style="left:712px"><div class="shot" role="img" aria-label="LED spot bulb with pin base"></div><div class="label">Product 4</div></div>
  <div class="product" style="left:904px"><div class="shot" role="img" aria-label="LED spotlight bulb"></div><div class="label">Product 5</div></div>
</section>

<footer class="site-footer">
  <div class="footer-brand"><span class="brand-dot"></span><span class="brand-name">BRIGHTQUOKKA</span></div>

  <div class="testimonial">
    <svg width="64" height="44" viewBox="0 0 64 44" style="position:absolute;left:14px;top:0">
      <ellipse cx="24" cy="18" rx="20" ry="14" fill="#3fac48"/>
      <path d="M14 28 L8 38 L24 30 Z" fill="#3fac48"/>
      <ellipse cx="40" cy="24" rx="18" ry="12" fill="#6fd36a"/>
      <path d="M46 34 L54 42 L50 32 Z" fill="#6fd36a"/>
    </svg>
    <h3>Testimonial</h3>
    <span class="quote-mark">&ldquo;</span>
    <blockquote>I have been very satisfied with all staff and the service and attention they have provided. Most importantly the outcome has been very satisfactory."-</blockquote>
    <cite>Petra K.</cite>
  </div>

  <div class="newsletter">
    <svg width="42" height="40" viewBox="0 0 42 40" style="position:absolute;left:0;top:0">
      <rect x="2" y="12" width="34" height="24" fill="#e8eef4" stroke="#8aa" stroke-width="1.5"/>
      <path d="M2 12 L19 26 L36 12" fill="none" stroke="#8aa" stroke-width="1.5"/>
      <path d="M14 36 L36 6 L40 9 L18 38 Z" fill="#333"/>
    </svg>
    <h3>Subscribe to newsletter</h3>
    <p>Lorem Ipsum is simply dummy text of the printing and typesetting</p>
    <div class="field">Enter Newsletter</div>
    <div class="social">
      <span style="background:#2f5fa8"></span>
      <span style="background:#1f4f86"></span>
      <span style="background:#f07a1a"></span>
      <span style="background:#4ab3e6"></span>
    </div>
    <div class="subscribe">Subscribe</div>
  </div>
</footer>

<div class="base-line"></div>

</body>
</html>
```